A Modern & Sleek "Coming Soon" Page for an A.I Recruiting App

For the “Coming Soon” website, a simple background with no people in it. I've attached an A.I image of what the page should generally look like.

- A single mobile phone as the main focus where the user actually clicks on the, “notify me” button (after entering their email address).
- In the background where the pillars/columns are seen in the example, should be subtle pad locks that are in their opened position with a key inside the lock. I've attached images to try to illustrate this idea, but they are far away in style from what I'm looking for.

SLOGAN: Unlocking the power of meaningful connections
LOGO/TITLE: Should be the name as shown in image with only the name "KelvoLink" on it
COLORS: Purplish/blue hues. Should not be too feminine
NOTE: The user should only click once when signing up/entering their email.

Product: A recruiting platform that matches employers/employees with A.I. and prioritizing cultural fit/values system before skills. The industry we are tackling first is the caregiving industry (nannies, tutors, elderly). All users will be background screened and that info lives on the blockchain. All users will have the option to review and be reviewed/rated.

```html
<!DOCTYPE html>
<html lang="en">
<head>
<meta charset="UTF-8">
<title>KelvoLink — Coming Soon</title>
<link rel="stylesheet" href="https://fonts.googleapis.com/css2?family=Montserrat:wght@200;400;700&family=Michroma&display=swap">
<style>
  :root {
    --bg-top: #0b0318;
    --bg-bottom: #1a0637;
    --white: #ffffff;
    --soft-white: rgba(255,255,255,0.82);
    --lock-violet: #5b22d6;
    --lock-deep: #2a0c66;
    --phone-body: #1a0b2e;
    --screen-top: #6a3aa3;
    --screen-mid: #43207a;
    --screen-bottom: #1e0c3a;
  }
  * { margin: 0; padding: 0; box-sizing: border-box; }
  html, body { width: 1200px; height: 667px; overflow: hidden; }
  body {
    position: relative;
    background:
      radial-gradient(ellipse 420px 320px at 820px 330px, rgba(58,15,122,0.5), transparent 70%),
      linear-gradient(180deg, var(--bg-top) 0%, var(--bg-bottom) 100%);
    color: var(--white);
    font-family: "Michroma", sans-serif;
  }

  /* header */
  .brand-logo {
    position: absolute;
    left: 110px; top: 40px;
    font-family: "Montserrat", sans-serif;
    font-weight: 200;
    font-size: 64px;
    letter-spacing: 7px;
    line-height: 1;
  }
  .menu-icon { position: absolute; left: 863px; top: 63px; width: 21px; height: 18px; }
  .signup-button {
    position: absolute;
    left: 939px; top: 42px;
    width: 150px; height: 59px;
    border: 1px solid var(--white);
    display: flex; align-items: center; justify-content: center;
    font-size: 17px; letter-spacing: 0.3px;
    -webkit-text-stroke: 0.5px var(--white);
    color: var(--white); text-decoration: none;
  }

  /* background padlock */
  .lock-art {
    position: absolute;
    left: 610px; top: 100px; width: 440px; height: 460px;
    border-radius: 40% 40% 18% 18%;
    background: radial-gradient(ellipse at 45% 35%, rgba(91,34,214,0.5), rgba(42,12,102,0.3) 55%, transparent 75%);
  }

  /* phone */
  .phone {
    position: absolute;
    left: 148px; top: 140px; width: 272px; height: 500px;
    border-radius: 42px;
    background: var(--phone-body);
    padding: 9px;
    transform: rotate(-7deg);
    box-shadow: 0 0 0 2px #3a1f5e, 0 0 40px rgba(90,45,143,0.45);
  }
  .phone-screen {
    position: relative;
    width: 100%; height: 100%;
    border-radius: 34px;
    overflow: hidden;
    background: linear-gradient(175deg, var(--screen-top) 0%, var(--screen-mid) 45%, var(--screen-bottom) 100%);
    text-align: center;
    font-family: "Montserrat", sans-serif;
  }
  .phone-notch {
    position: absolute;
    left: 50%; top: 0;
    width: 112px; height: 24px;
    transform: translateX(-50%);
    background: var(--phone-body);
    border-radius: 0 0 16px 16px;
  }
  .phone-logo {
    position: absolute; left: 0; right: 0; top: 112px;
    font-weight: 200; font-size: 19px; letter-spacing: 2px;
  }
  .phone-slogan {
    position: absolute; left: 0; right: 0; top: 258px;
    font-weight: 400; font-size: 12px; line-height: 17px;
    color: var(--soft-white);
  }
  .phone-email {
    position: absolute; left: 40px; right: 40px; top: 330px;
    height: 30px;
    border: none; border-bottom: 1px solid rgba(255,255,255,0.55);
    background: transparent;
    color: var(--white);
    font-family: "Montserrat", sans-serif; font-size: 11px;
    text-align: center;
  }
  .phone-email::placeholder { color: rgba(255,255,255,0.6); }
  .phone-notify {
    position: absolute; left: 42px; right: 42px; top: 385px;
    height: 36px;
    border: 2px solid rgba(255,255,255,0.85);
    border-radius: 18px;
    background: rgba(255,255,255,0.08);
    display: flex; align-items: center; justify-content: center;
    font-weight: 700; font-size: 15px;
    color: var(--white);
  }
  .phone-note {
    position: absolute; left: 0; right: 0; top: 432px;
    font-size: 10px; line-height: 13px;
    color: var(--soft-white);
  }

  /* hero */
  .hero { position: absolute; left: 536px; top: 222px; }
  .hero-title {
    font-size: 29px; font-weight: 400; letter-spacing: 0.3px;
    -webkit-text-stroke: 0.8px var(--white);
    line-height: 1;
  }
  .hero-slogan {
    margin-top: 40px;
    font-size: 28px; font-weight: 400;
    line-height: 72px;
    -webkit-text-stroke: 0.8px var(--white);
    white-space: nowrap;
  }
  .notify-button {
    position: absolute;
    left: 537px; top: 468px;
    width: 183px; height: 65px;
    border: 1px solid var(--white);
    display: flex; align-items: center; justify-content: center;
    font-size: 18px; letter-spacing: 0.3px;
    -webkit-text-stroke: 0.5px var(--white);
    color: var(--white); text-decoration: none;
  }
</style>
</head>
<body>
  <div class="lock-art" role="img" aria-label="Glowing violet open padlock with a key in its lock"></div>

  <div class="phone">
    <div class="phone-screen">
      <div class="phone-notch"></div>
      <div class="phone-logo">KELVOLINK</div>
      <p class="phone-slogan">Unlocking power of<br>meaningful connections</p>
      <input class="phone-email" type="email" placeholder="Your email address" aria-label="Email address">
      <div class="phone-notify">Notify Me</div>
      <p class="phone-note">Enter your email<br>for early access</p>
    </div>
  </div>

  <header>
    <div class="brand-logo">KELVOLINK</div>
    <svg class="menu-icon" viewBox="0 0 21 18" aria-label="Menu">
      <rect x="0" y="1" width="21" height="2.5" fill="#fff"/>
      <rect x="0" y="7.75" width="21" height="2.5" fill="#fff"/>
      <rect x="0" y="14.5" width="21" height="2.5" fill="#fff"/>
    </svg>
    <a class="signup-button" href="#">SIGN UP</a>
  </header>

  <main class="hero">
    <h2 class="hero-title">KELVOLINK</h2>
    <h1 class="hero-slogan">UNLOCKING THE POWER OF<br>MEANINGFUL CONNECTIONS</h1>
  </main>
  <a class="notify-button" href="#">NOTIFY ME</a>
</body>
</html>
```